Business Card Design

We need a business card designed for our new company. Prefer a black card with white logo & writing.

Contact Information for Business Card

Ted Galloway, address: 7-4812 Fernhollow Road, Abbotsford, BC, V3K 8R2, Office Phone: 604-712-3390, Cell: 604-947-2164, Email: ted@resinworkshub.ca

Colors

Designer to choose only greyscale colors for use in the design.

```html
<!DOCTYPE html>
<html lang="en">
<head>
<meta charset="utf-8">
<title>Resinworks Hub — Business Card</title>
<link href="https://fonts.googleapis.com/css2?family=Montserrat:wght@400;500;700;800&display=swap" rel="stylesheet">
<style>
  :root {
    --backdrop: #2a2a2a;
    --card-black: #1d1d1d;
    --gloss-black: #0c0c0c;
    --card-white: #ffffff;
    --ink: #111111;
    --ink-soft: #333333;
  }
  * { margin: 0; padding: 0; box-sizing: border-box; }
  html, body {
    width: 1200px; height: 1200px; overflow: hidden;
    background: var(--backdrop);
    font-family: "Montserrat", sans-serif;
  }
  .canvas { position: relative; width: 1200px; height: 1200px; }
  .card {
    position: absolute; left: 150px; width: 900px; height: 514px;
    overflow: hidden;
  }
  .card--back { top: 70px; background: var(--card-black); }
  .card--front { top: 620px; background: var(--card-white); color: var(--ink); }

  .brand {
    display: flex; align-items: center; gap: 14px;
    font-weight: 800; letter-spacing: 0.02em; text-transform: uppercase;
    white-space: nowrap;
  }
  .brand__dot { width: 18px; height: 18px; border-radius: 50%; background: currentColor; }
  .card--back .brand {
    position: absolute; left: 50%; top: 50%; transform: translate(-50%, -50%);
    color: var(--gloss-black); font-size: 58px;
  }
  .card--front .brand {
    position: absolute; left: 48px; top: 70px;
    color: var(--ink); font-size: 40px;
  }

  .contact {
    position: absolute; left: 540px; top: 200px; width: 340px;
  }
  .contact__name { font-weight: 700; font-size: 30px; letter-spacing: 0.01em; }
  .contact__role { font-size: 17px; color: var(--ink-soft); margin-top: 4px; }
  .contact__address { font-size: 19px; line-height: 1.3; margin-top: 28px; }
  .contact__list { list-style: none; margin-top: 14px; }
  .contact__item {
    display: flex; align-items: center; gap: 14px;
    font-size: 19px; line-height: 1.6;
  }
  .contact__icon { width: 18px; height: 18px; flex: none; fill: var(--ink); }
  .contact__item--plain { padding-left: 32px; }
</style>
</head>
<body>
<main class="canvas">
  <section class="card card--back" aria-label="Card back">
    <div class="brand"><span class="brand__dot"></span>Resinworks Hub</div>
  </section>

  <section class="card card--front" aria-label="Card front">
    <div class="brand"><span class="brand__dot"></span>Resinworks Hub</div>

    <div class="contact">
      <p class="contact__name">Ted Galloway</p>
      <p class="contact__role">owner</p>
      <p class="contact__address">7-4812 Fernhollow Road,<br>Abbotsford, BC, V3K 8R2</p>
      <ul class="contact__list">
        <li class="contact__item">
          <svg class="contact__icon" viewBox="0 0 24 24" aria-hidden="true"><path d="M6.6 10.8a15 15 0 0 0 6.6 6.6l2.2-2.2a1 1 0 0 1 1-.25 11.4 11.4 0 0 0 3.6.57 1 1 0 0 1 1 1V20a1 1 0 0 1-1 1A17 17 0 0 1 3 4a1 1 0 0 1 1-1h3.5a1 1 0 0 1 1 1c0 1.25.2 2.45.57 3.57a1 1 0 0 1-.25 1z"/></svg>
          604-712-3390
        </li>
        <li class="contact__item">
          <svg class="contact__icon" viewBox="0 0 24 24" aria-hidden="true"><path d="M7 1h10a2 2 0 0 1 2 2v18a2 2 0 0 1-2 2H7a2 2 0 0 1-2-2V3a2 2 0 0 1 2-2zm0 3v15h10V4zm5 16a1 1 0 1 0 0 2 1 1 0 0 0 0-2z"/></svg>
          604-947-2164
        </li>
        <li class="contact__item">
          <svg class="contact__icon" viewBox="0 0 24 24" aria-hidden="true"><path d="M2 5h20v14H2zm2 2v.5l8 5 8-5V7l-8 5z"/></svg>
          ted@resinworkshub.ca
        </li>
        <li class="contact__item">
          <svg class="contact__icon" viewBox="0 0 24 24" aria-hidden="true"><path d="M12 2a10 10 0 1 0 0 20 10 10 0 0 0 0-20zm-1 17.9A8 8 0 0 1 4.1 11H7c.1 3.2 1.5 6.3 4 8.9zM7 9H4.1A8 8 0 0 1 11 4.1C8.5 6.7 7.1 9.8 7 9zm6 10.9c2.5-2.6 3.9-5.7 4-8.9h2.9a8 8 0 0 1-6.9 8.9zM17 9c-.1-.8-1.5-2.3-4-4.9A8 8 0 0 1 19.9 9zm-8 2h6c-.1 2.7-1.2 5.3-3 7.5C10.2 16.3 9.1 13.7 9 11zm0-2c.1-2.7 1.2-5.3 3-7.5 1.8 2.2 2.9 4.8 3 7.5z"/></svg>
          www.resinworkshub.ca
        </li>
        <li class="contact__item contact__item--plain">www.resinworkshub.ca</li>
      </ul>
    </div>
  </section>
</main>
</body>
</html>
```